Wordpress - For IT, Cloud/Hosting, Residential/Commercial Construction Services

We are a holding company for service companies. We want the current Wordpress site modified or a new wordpress site completed. We want this site to be the parent website, that then has pull down menus linking to our other website (currently http://brightwallfix.com, http://q7v.host and would like it to be easy and fluid as we acquire more companies as we have with TKLS, Inc., B&J Construction, Brightwall Fix etc. Model after sites like Pemrose.com, Tallowbine.com, QDV.com,.vanterelm.com

------

The parent is the main site q7v Corp. Below that are sub corps and DBAs. q7v Corp stands for Quick 7 Venture Corp. q7v Offers IT manages services, 24x7 support, Monitoring NOC, Remote Hands, Onsite support services. We have acquired TKLS, Inc, B & J Construction, BrightwallFix.com. We plan to acquire/spin up many companies that offer service, support and installation offerings and will all be known as an q7v Corp Company for branding purposes. We recently had our logo done, but then ran it through 3d glass as we like the look better than the original works. We have original files in vector, but not the 3D galss door render.

Target Market(s)

IT Server and Desktop Support. Construction. Mold Remediation. Mergers and Acquisitions.

Industry/Entity Type

It Company

Coding

Coded - Design and coding required

Font styles to use
Sans Serif

Colors
0792cd

Requirements
Must have
• Clean interface. Modern design. Mobile device and multi browser support. Must be for Wordpress. Job posting with resume submission module.Hook to our Web hosting portal (Tormund) API into VexaLine Reseller portal, customer portal to allow payments to their account etc.. Easy to edit. Easy to add to, Press Release Section, Investor Relations etc.
Should not have
• Slow loading. Played out design. Over use of stock images. Copied from a competitor or something point to such.

```html
<!DOCTYPE html>
<html lang="en">
<head>
<meta charset="utf-8">
<title>Q7V Corp</title>
<link href="https://fonts.googleapis.com/css2?family=Poppins:wght@400;500;600&family=Open+Sans:wght@400;600&display=swap" rel="stylesheet">
<style>
:root{
  --hero-dark:#0a2a8c;
  --hero-mid:#1547c4;
  --hero-light:#2f6ee6;
  --accent:#1f6fd6;
  --button:#1c5cb5;
  --ink:#1b1b1b;
  --muted:#555b66;
  --pale:#e8f1fb;
  --footer:#050505;
  --footer-text:#ffffff;
  --line:#1d5fd1;
}
*{margin:0;padding:0;box-sizing:border-box}
html,body{width:1200px;height:4100px;overflow:hidden}
body{position:relative;background:#fff;font-family:"Open Sans",sans-serif;color:var(--ink)}
.abs{position:absolute}
h1,h2,h3,.nav,.btn{font-family:"Poppins",sans-serif}

/* header / hero */
.hero{left:0;top:0;width:1200px;height:600px}
.logo-text{font-family:"Poppins",sans-serif;font-weight:600;color:#fff;font-size:42px;letter-spacing:2px}
.nav{display:flex;gap:38px;color:#fff;font-size:17px;top:82px;right:88px}
.phone{top:34px;right:180px;color:#fff;font-size:19px;display:flex;align-items:center;gap:8px}
.login{top:28px;right:88px;border:2px solid #fff;border-radius:20px;color:#fff;font-size:16px;padding:4px 20px;font-family:"Poppins",sans-serif}
.hero-title{left:87px;top:228px;color:#fff;font-size:41px;font-weight:500;white-space:nowrap;z-index:2}
.hero-sub{left:87px;top:290px;color:#fff;font-size:23px;font-family:"Poppins",sans-serif;z-index:2}
.btn{display:inline-block;border-radius:22px;font-size:16px;font-weight:500;text-align:center}
.btn-white{left:92px;top:354px;width:180px;height:40px;line-height:40px;background:#fff;color:var(--ink)}
.dots{left:94px;top:458px;display:flex;gap:8px}
.dots span{width:22px;height:22px;border-radius:50%;background:#111;color:#fff;font-size:13px;line-height:22px;text-align:center}
.hero-art{left:615px;top:180px;width:500px;height:570px;border-radius:30px;background:linear-gradient(160deg,#dfeaff 0%,#8fb4f5 55%,#3e6fd8 100%)}

/* about */
.about-mark{left:90px;top:900px;width:325px;height:110px;font-family:"Poppins",sans-serif;font-weight:600;font-size:96px;color:#16305e;line-height:110px}
.divider{left:459px;top:808px;width:2px;height:310px;background:#9aa4b2}
.about-title{left:492px;top:798px;font-size:46px;font-weight:400}
.blue{color:var(--accent)}
.about-text{left:492px;top:872px;width:620px;font-size:15px;line-height:25px;color:#333}
.btn-outline{border:2px solid var(--button);color:var(--button);width:130px;height:36px;line-height:32px}

/* services */
.services{left:0;top:1197px;width:1200px;height:842px;background:var(--pale)}
.sec-title{width:1200px;text-align:center;font-size:46px;font-weight:400;left:0}
.svc-intro{left:150px;top:1378px;width:900px;text-align:center;font-size:15px;line-height:29px;color:#333}
.card{top:1525px;width:278px;height:383px;background:#fff;border-radius:20px;box-shadow:0 4px 18px rgba(20,60,120,.18);text-align:center;padding-top:40px}
.card svg{display:block;margin:0 auto}
.card h3{font-size:21px;font-weight:500;margin-top:28px}
.card p{font-size:13px;line-height:22px;color:#555;width:210px;margin:20px auto 0}
.btn-blue{background:var(--button);color:#fff;width:172px;height:40px;line-height:40px;margin-top:18px}
.arrow{top:1697px;width:44px;height:44px;border-radius:50%;background:#fff;box-shadow:0 2px 8px rgba(0,0,0,.15);text-align:center;line-height:44px;font-size:22px;color:#333}

/* holding */
.hold-kicker{left:123px;top:2188px;font-family:"Poppins",sans-serif;font-size:32px;color:var(--accent)}
.hold-title{left:123px;top:2225px;font-size:46px;font-weight:400}
.hold-list{left:128px;top:2288px;list-style:none;font-size:16px;line-height:34px;color:#333}
.hold-list li{display:flex;align-items:center;gap:12px}
.hold-list li::before{content:"›";width:16px;height:16px;border-radius:50%;background:#1a3f91;color:#fff;font-size:13px;line-height:15px;text-align:center}
.btn-hold{left:116px;top:2468px;width:142px;height:40px;line-height:40px}
.video-back{left:656px;top:2181px;width:451px;height:306px;background:#1e7fe0}
.video{left:629px;top:2208px;width:453px;height:304px;background:linear-gradient(135deg,#1d2b40,#4c6e93 55%,#1a2434)}
.play{left:830px;top:2335px}

/* blog */
.blog{left:0;top:2665px;width:1200px;height:732px;background:var(--pale)}
.feature{left:123px;top:2886px;width:456px;height:380px;background:#fff;box-shadow:0 3px 14px rgba(0,0,0,.1)}
.feature-img{width:456px;height:224px;background:linear-gradient(180deg,#b9cde6,#eef3f9 60%,#c7d2de)}
.feature h3{font-size:15px;font-weight:500;margin:30px 28px 0}
.feature p{font-size:12.5px;line-height:20px;color:#666;margin:10px 28px 0}
.feature a{font-size:12.5px;color:var(--accent);margin:10px 28px 0;display:block;text-decoration:none}
.post{left:627px;width:470px;height:112px;border-bottom:1px solid #cfd8e3}
.post .thumb{position:absolute;left:0;top:0;width:155px;height:104px}
.post h3{position:absolute;left:193px;top:4px;font-size:14px;font-weight:500}
.post p{position:absolute;left:193px;top:28px;width:270px;font-size:12px;line-height:19px;color:#555}
.post .meta{position:absolute;left:193px;top:78px;display:flex;gap:14px}

/* partners */
.partner{top:3485px;width:170px;height:95px;background:#f4f4f4;border:1px solid #ddd;display:flex;align-items:center;justify-content:center}
.partner span{width:110px;height:22px;border-radius:4px;background:#b5b5b5}

/* footer */
.footer-line{left:0;top:3695px;width:1200px;height:10px;background:var(--line)}
.footer{left:0;top:3705px;width:1200px;height:395px;background:var(--footer)}
.f-logo{left:178px;top:3815px;font-family:"Poppins",sans-serif;font-weight:600;font-size:58px;color:#2f6fe0}
.socials{left:158px;top:3922px;display:flex;gap:16px}
.socials span{width:26px;height:26px;border-radius:4px;background:#fff}
.f-head{font-family:"Poppins",sans-serif;font-size:21px;top:3788px;color:var(--footer-text)}
.f-item{display:flex;gap:14px;font-size:13px;line-height:20px;color:var(--footer-text)}
.f-item strong{font-weight:600;font-size:14px;display:block}
.f-links{list-style:none;font-size:14px;line-height:33px;top:3826px;color:var(--footer-text)}
.copy{left:0;width:1200px;top:4032px;text-align:center;font-size:14px;color:#ccc}
</style>
</head>
<body>

<!-- hero -->
<svg class="abs hero" viewBox="0 0 1200 600" aria-hidden="true">
  <defs>
    <linearGradient id="heroGrad" x1="0" y1="0" x2="1" y2="1">
      <stop offset="0" stop-color="#1547c4"/>
      <stop offset=".6" stop-color="#2f6ee6"/>
      <stop offset="1" stop-color="#0a2a8c"/>
    </linearGradient>
  </defs>
  <path d="M0 0H1200V420C1000 560 700 540 420 560C250 575 100 600 0 590Z" fill="url(#heroGrad)"/>
  <path d="M0 590C100 600 250 575 420 560C700 540 1000 560 1200 420V445C1000 580 700 560 420 578C250 590 100 610 0 600Z" fill="#0a2a8c"/>
</svg>
<div class="abs logo-text" style="left:87px;top:28px">Q7V</div>
<div class="abs phone"><svg width="18" height="18" viewBox="0 0 24 24"><path d="M6.6 10.8a15 15 0 0 0 6.6 6.6l2.2-2.2c.3-.3.7-.4 1-.2 1.1.4 2.3.6 3.6.6.6 0 1 .4 1 1V20c0 .6-.4 1-1 1A17 17 0 0 1 3 4c0-.6.4-1 1-1h3.5c.6 0 1 .4 1 1 0 1.3.2 2.5.6 3.6.1.3 0 .7-.2 1z" fill="#fff"/></svg>888-410-7392</div>
<div class="abs login">Login</div>
<nav class="abs nav"><span>Home</span><span>Company ▾</span><span>About us</span><span>Services</span><span>Blog</span><span>Contact Us</span></nav>
<div class="abs hero-art" role="img" aria-label="Isometric illustration of people working on cloud servers and devices"></div>
<h1 class="abs hero-title">Cloud &amp; Hosting Services</h1>
<div class="abs hero-sub">Neque porro quisquam est qui dolorem</div>
<div class="abs btn btn-white">Get Started Now</div>
<div class="abs dots"><span>‹</span><span>›</span></div>

<!-- about -->
<div class="abs about-mark">Q7V</div>
<div class="abs divider"></div>
<h2 class="abs about-title">About <span class="blue">Q7V Corp</span></h2>
<p class="abs about-text">q7v Corp is a Corvane and Tallowbine IT Solution Provider. We provide support for Desktops, Laptops, Tablets, Mobile Devices, Networking, WiFi, Server, Design and more by providing Remote and OnSite Support Services.<br>q7v Corp (Quick 7 Venture) Full service one stop shop service provider. Our CEO and Founder Leon Sarker has been working with Tallowbine Solutions all the way back to Kestrel OS and all the way to Tallowbine's full solution offerings of today. He trains his team to be clones of his highly technical mindset of "can do it all aptitude"</p>
<div class="abs btn btn-outline" style="left:492px;top:1070px">Read More</div>

<!-- services -->
<div class="abs services"></div>
<h2 class="abs sec-title" style="top:1300px">Our <span class="blue">Services</span></h2>
<p class="abs svc-intro">It is a long established fact that a reader will be distracted by the readable content of a page when looking at its layout. The point of using Lorem Ipsum is that it has a more-or-less normal distribution of letters, as opposed to using 'Content here, content here', making it look like readable English.</p>
<div class="abs arrow" style="left:74px">‹</div>
<div class="abs arrow" style="left:1082px">›</div>

<div class="abs card" style="left:137px">
  <svg width="90" height="90" viewBox="0 0 90 90" fill="none" stroke="#1f5fb8" stroke-width="2.5"><path d="M25 60a14 14 0 0 1 2-28 20 20 0 0 1 38 4 12 12 0 0 1-2 24Z"/><rect x="32" y="14" width="26" height="10"/><path d="M45 60v14M30 60v10M60 60v10"/><circle cx="45" cy="78" r="3"/><circle cx="30" cy="73" r="3"/><circle cx="60" cy="73" r="3"/></svg>
  <h3>Cloud &amp; Hosting</h3>
  <p>The point of using Lorem Ipsum is that it has a more-or-less normal distribution of letters, as opposed to using</p>
  <div class="btn btn-blue">Read More</div>
</div>
<div class="abs card" style="left:451px">
  <svg width="90" height="90" viewBox="0 0 90 90" fill="none" stroke="#1f5fb8" stroke-width="2.5"><path d="M15 60l40-40 15 15-40 40H15Z"/><path d="M22 68l10-10M30 76l8-8"/><path d="M55 20l10-10 15 15-10 10"/><path d="M14 82h62"/></svg>
  <h3>Construction</h3>
  <p>The point of using Lorem Ipsum is that it has a more-or-less normal distribution of letters, as opposed to using</p>
  <div class="btn btn-blue">Read More</div>
</div>
<div class="abs card" style="left:776px">
  <svg width="90" height="90" viewBox="0 0 90 90" fill="none" stroke="#1f5fb8" stroke-width="2.5"><circle cx="40" cy="40" r="22"/><path d="M56 56l20 20"/><path d="M28 44l8-8 6 6 10-10"/><circle cx="40" cy="40" r="30" stroke-dasharray="4 6"/></svg>
  <h3>IT Services</h3>
  <p>The point of using Lorem Ipsum is that it has a more-or-less normal distribution of letters, as opposed to using</p>
  <div class="btn btn-blue">Read More</div>
</div>

<!-- holding -->
<div class="abs hold-kicker">Q7V Corp</div>
<h2 class="abs hold-title">Holding company</h2>
<ul class="abs hold-list">
  <li>Lorem ipsum dolor sit amet, consectetur adipiscing elit.</li>
  <li>Sed vel dui vel diam ultricies dignissim.</li>
  <li>Mauris eget purus eget ante congue egestas at ac mi</li>
  <li>Aliquam pretium quam rhoncus lectus porta euismod.</li>
  <li>Vestibulum non lacus a massa vestibulum mattis.</li>
</ul>
<div class="abs btn btn-blue btn-hold">Read More</div>
<div class="abs video-back"></div>
<div class="abs video" role="img" aria-label="Video still of technicians working in a server room"></div>
<svg class="abs play" width="50" height="50" viewBox="0 0 50 50"><circle cx="25" cy="25" r="24" fill="rgba(255,255,255,.35)" stroke="#fff" stroke-width="2"/><path d="M20 15l15 10-15 10Z" fill="#fff"/></svg>

<!-- blog -->
<div class="abs blog"></div>
<h2 class="abs sec-title" style="top:2757px">Latest <span class="blue">Blog</span></h2>
<div class="abs feature">
  <div class="feature-img" role="img" aria-label="Photo of a hand touching a cloud network diagram"></div>
  <h3>Neque porro quisquam est qui dolorem</h3>
  <p>The point of using Lorem Ipsum is that it has a more-or-less normal distribution of letters, as opposed to using 'Content</p>
  <a>Read More ›</a>
</div>
<div class="abs post" style="top:2891px">
  <div class="thumb" role="img" aria-label="Photo of server racks" style="background:linear-gradient(135deg,#3a3020,#8a7a5a,#2a2a2a)"></div>
  <h3>Neque porro quisquam est</h3>
  <p>The point of using Lorem Ipsum is that it has a more-or-less normal distribution of letters</p>
  <div class="meta"><svg width="14" height="14" viewBox="0 0 24 24" fill="none" stroke="#888" stroke-width="2"><path d="M12 2l3 7 7 .5-5.5 4.5 2 7L12 17l-6.5 4 2-7L2 9.5 9 9Z"/></svg><svg width="14" height="14" viewBox="0 0 24 24" fill="none" stroke="#888" stroke-width="2"><rect x="3" y="5" width="18" height="16"/><path d="M3 10h18"/></svg><svg width="14" height="14" viewBox="0 0 24 24" fill="none" stroke="#888" stroke-width="2"><circle cx="12" cy="8" r="4"/><path d="M4 21c1-5 15-5 16 0"/></svg></div>
</div>
<div class="abs post" style="top:3025px">
  <div class="thumb" role="img" aria-label="Photo of a blue lit data center" style="background:linear-gradient(135deg,#0e1d4a,#2c56a8,#0b1533)"></div>
  <h3>Porro quisquam est dolorem</h3>
  <p>The point of using Lorem Ipsum is that it has a more-or-less normal distribution of letters</p>
  <div class="meta"><svg width="14" height="14" viewBox="0 0 24 24" fill="none" stroke="#888" stroke-width="2"><path d="M12 2l3 7 7 .5-5.5 4.5 2 7L12 17l-6.5 4 2-7L2 9.5 9 9Z"/></svg><svg width="14" height="14" viewBox="0 0 24 24" fill="none" stroke="#888" stroke-width="2"><rect x="3" y="5" width="18" height="16"/><path d="M3 10h18"/></svg><svg width="14" height="14" viewBox="0 0 24 24" fill="none" stroke="#888" stroke-width="2"><circle cx="12" cy="8" r="4"/><path d="M4 21c1-5 15-5 16 0"/></svg></div>
</div>
<div class="abs post" style="top:3159px;border-bottom:none">
  <div class="thumb" role="img" aria-label="Photo of engineers inspecting network hardware" style="background:linear-gradient(135deg,#5b6a7a,#b5bcc4,#3a4450)"></div>
  <h3>Dolorem ipsum quia dolor</h3>
  <p>The point of using Lorem Ipsum is that it has a more-or-less normal distribution of letters</p>
  <div class="meta"><svg width="14" height="14" viewBox="0 0 24 24" fill="none" stroke="#888" stroke-width="2"><path d="M12 2l3 7 7 .5-5.5 4.5 2 7L12 17l-6.5 4 2-7L2 9.5 9 9Z"/></svg><svg width="14" height="14" viewBox="0 0 24 24" fill="none" stroke="#888" stroke-width="2"><rect x="3" y="5" width="18" height="16"/><path d="M3 10h18"/></svg><svg width="14" height="14" viewBox="0 0 24 24" fill="none" stroke="#888" stroke-width="2"><circle cx="12" cy="8" r="4"/><path d="M4 21c1-5 15-5 16 0"/></svg></div>
</div>

<!-- partners -->
<div class="abs partner" style="left:150px"><span></span></div>
<div class="abs partner" style="left:332px"><span></span></div>
<div class="abs partner" style="left:514px"><span></span></div>
<div class="abs partner" style="left:697px"><span></span></div>
<div class="abs partner" style="left:880px"><span></span></div>

<!-- footer -->
<div class="abs footer-line"></div>
<div class="abs footer"></div>
<div class="abs f-logo">Q7V</div>
<div class="abs socials"><span></span><span></span><span></span><span></span></div>

<div class="abs f-head" style="left:465px">CONTACT US</div>
<div class="abs f-item" style="left:465px;top:3835px">
  <svg width="20" height="16" viewBox="0 0 24 18" fill="none" stroke="#fff" stroke-width="1.8"><rect x="1" y="1" width="22" height="16"/><path d="M1 1l11 9 11-9"/></svg>
  <div><strong>EMAIL ADDRESS</strong>info@samplemail.com.au</div>
</div>
<div class="abs f-item" style="left:465px;top:3900px">
  <svg width="20" height="20" viewBox="0 0 24 24" fill="none" stroke="#fff" stroke-width="1.8"><path d="M6.6 10.8a15 15 0 0 0 6.6 6.6l2.2-2.2 4.6 1V20c0 .6-.4 1-1 1A17 17 0 0 1 3 4c0-.6.4-1 1-1h3.5l1 4.6z"/></svg>
  <div><strong>PHONE NUMBER</strong>0412 730 415</div>
</div>

<div class="abs f-head" style="left:754px">ABOUT</div>
<ul class="abs f-links" style="left:758px"><li>Home</li><li>About Us</li><li>Services</li><li>Blog</li></ul>

<div class="abs f-head" style="left:973px">RESOURCES</div>
<ul class="abs f-links" style="left:975px"><li>Contact Us</li><li>Privacy Policy</li><li>Terms of Use</li><li>FAQ</li></ul>

<div class="abs copy">Copyright © 2018. All Rights Reserved</div>

</body>
</html>
```